New website for concierge mobile medical service

new website for business:
WEBSITE REQUEST LIST:
Luxury product look.
Professional. Clean & simple, NO stock people photos. Graphics OK.
Black and white text.

```html
<!DOCTYPE html>
<html lang="en">
<head>
<meta charset="utf-8">
<title>Pricing – Vela Health</title>
<link href="https://fonts.googleapis.com/css2?family=Lato:wght@400;700;900&family=Ubuntu:wght@400;500;700&display=swap" rel="stylesheet">
<style>
:root{
  --ink:#1c1c1c;
  --purple:#7a72b8;
  --teal-dark:#0f5a72;
  --teal-mid:#1a93b0;
  --navy:#011522;
  --card-top:#5470b8;
  --card-bottom:#968bc6;
  --footer:#2a2a2a;
  --white:#ffffff;
  --button-light:#9ad6df;
}
*{box-sizing:border-box;margin:0;padding:0}
html,body{width:1167px;height:1200px;overflow:hidden;background:var(--white)}
body{font-family:'Lato',sans-serif;color:var(--ink);position:relative}
.header{position:absolute;left:0;top:0;width:1167px;height:104px;background:var(--white);z-index:2}
.brand{position:absolute;left:154px;top:20px;width:116px;height:116px;border-radius:50%;background:var(--navy);border:6px solid var(--white);box-shadow:0 0 0 3px #6fc2d8;display:flex;align-items:center;justify-content:center;color:var(--white);font-family:'Lato',sans-serif;font-weight:700;font-size:17px}
.phone{position:absolute;left:863px;top:16px;display:flex;align-items:center;gap:12px}
.phone-icon{width:31px;height:31px;background:var(--purple);display:flex;align-items:center;justify-content:center}
.phone-number{color:var(--purple);font-weight:700;font-size:19px}
.main-nav{position:absolute;top:74px;left:0;width:100%}
.main-nav a{position:absolute;font-size:12px;font-weight:700;color:var(--ink);text-decoration:none;white-space:nowrap}
.main-nav a.faq{color:var(--teal-dark)}
.nav-active{position:absolute;left:794px;top:99px;width:65px;height:5px;background:var(--teal-dark)}
.hero{position:absolute;left:0;top:104px;width:1167px;height:258px;background:linear-gradient(100deg,#010c14 0%,#022338 45%,#0a4a6e 100%)}
.hero h1{position:absolute;left:140px;top:103px;font-size:44px;font-weight:900;color:var(--white);letter-spacing:.5px}
.hero-badge{position:absolute;left:841px;top:29px;width:200px;height:200px;border-radius:50%;border:3px solid #8ed8ee;background:radial-gradient(circle,#0d4f73 0%,#063552 70%)}
.intro{position:absolute;left:0;top:403px;width:1167px;text-align:center;font-size:18px;line-height:26px;color:#333}
.plan{position:absolute;top:480px;width:278px;height:257px;background:linear-gradient(180deg,var(--card-top),var(--card-bottom));color:var(--white);text-align:center}
.plan h2{font-family:'Ubuntu',sans-serif;font-weight:500;font-size:23px;margin-top:18px}
.plan-icon{width:44px;height:44px;margin:12px auto 0;border-radius:50%;background:rgba(255,255,255,.9)}
.price{font-family:'Ubuntu',sans-serif;font-weight:700;font-size:42px;margin-top:12px;line-height:1}
.price sup{font-size:20px;vertical-align:18px}
.price small{font-size:20px}
.plan-note{font-size:14px;line-height:22px;margin-top:16px;padding:0 16px}
.subscribe-button{position:absolute;left:25px;top:233px;width:228px;height:46px;background:linear-gradient(180deg,#0a3e57,#0f5e78);color:var(--white);font-family:'Ubuntu',sans-serif;font-weight:500;font-size:18px;line-height:46px}
.subscribe{position:absolute;left:0;top:824px;width:1167px;height:245px;background:linear-gradient(90deg,#1a9bb5 0%,#167f9c 50%,#1695b3 100%)}
.subscribe h2{position:absolute;width:100%;top:42px;text-align:center;font-family:'Ubuntu',sans-serif;font-weight:500;font-size:31px;color:var(--white)}
.field{position:absolute;top:100px;height:43px;width:309px;background:var(--white);font-size:12px;color:#333;padding:14px 14px}
.submit{position:absolute;left:268px;top:152px;width:631px;height:43px;background:var(--button-light);color:var(--white);text-align:center;font-weight:700;font-size:16px;line-height:43px}
.footer{position:absolute;left:0;top:1069px;width:1167px;height:131px;background:var(--footer);color:var(--white);text-align:center}
.footer-nav{margin-top:23px;font-size:12px;font-weight:700}
.footer-nav span{margin:0 18px}
.copyright{font-size:11px;margin-top:15px}
.social{display:flex;justify-content:center;gap:17px;margin-top:15px}
.social span{width:16px;height:16px;border-radius:50%;background:var(--white)}
</style>
</head>
<body>
<header class="header">
  <div class="brand">Vela Health</div>
  <div class="phone">
    <div class="phone-icon">
      <svg width="16" height="16" viewBox="0 0 24 24"><path fill="#fff" d="M6.6 10.8a15 15 0 0 0 6.6 6.6l2.2-2.2a1 1 0 0 1 1-.25 11.4 11.4 0 0 0 3.6.57 1 1 0 0 1 1 1V20a1 1 0 0 1-1 1A17 17 0 0 1 3 4a1 1 0 0 1 1-1h3.5a1 1 0 0 1 1 1c0 1.25.2 2.45.57 3.57a1 1 0 0 1-.25 1z"/></svg>
    </div>
    <span class="phone-number">555-014-2290</span>
  </div>
  <nav class="main-nav">
    <a style="left:384px">HOME</a>
    <a style="left:461px">ABOUT US</a>
    <a style="left:563px">WHY VELA?</a>
    <a style="left:676px">SERVICE AREA</a>
    <a style="left:803px">OTHER</a>
    <a class="faq" style="left:885px">FAQ</a>
    <a style="left:948px">CONTACT US</a>
  </nav>
  <div class="nav-active"></div>
</header>

<section class="hero">
  <h1>PRICING</h1>
  <div class="hero-badge" role="img" aria-label="Line illustration of a car with a medical caduceus above it"></div>
</section>

<p class="intro">Now accepting new patients with full mobile care starting March 1, 2020<br>New patients will have immediate access to Vela Health mobile urgent care for $50/month.</p>

<article class="plan" style="left:141px">
  <h2>Individual</h2>
  <div class="plan-icon" role="img" aria-label="Single person icon"></div>
  <p class="price"><sup>$</sup>300/<small>mo.</small></p>
  <div class="subscribe-button">Subscribe Today</div>
</article>
<article class="plan" style="left:445px">
  <h2>Married Couple</h2>
  <div class="plan-icon" role="img" aria-label="Couple icon"></div>
  <p class="price"><sup>$</sup>400/<small>mo.</small></p>
  <div class="subscribe-button">Subscribe Today</div>
</article>
<article class="plan" style="left:749px">
  <h2>Child with Adult</h2>
  <div class="plan-icon" role="img" aria-label="Adult with child icon"></div>
  <p class="price"><sup>$</sup>75/<small>ea.mo.</small></p>
  <p class="plan-note">Pricing is for each child added to an adult subscription</p>
  <div class="subscribe-button">Subscribe Today</div>
</article>

<section class="subscribe" role="img" aria-label="Teal medical network pattern background">
  <h2>Subscribe</h2>
  <div class="field" style="left:268px">Enter Name</div>
  <div class="field" style="left:590px">Enter Email Address</div>
  <div class="submit">SUBSCRIBE NOW</div>
</section>

<footer class="footer">
  <div class="footer-nav"><span>HOME</span><span>ABOUT US</span><span>WHY VELA?</span><span>SERVICE AREA</span><span>OTHER</span><span>CONTACT US</span></div>
  <p class="copyright">Copyright © 2019. Company Name All Rights Reserved</p>
  <div class="social"><span></span><span></span><span></span><span></span><span></span></div>
</footer>
</body>
</html>
```